Tradelume.ai

Australian based application building technology company. website (tradelume.ai) servicing the retail and shopping industries, IoT
Similar services to https://vextrio.com/.
Logo attached

Target Market(s)

Technology Retail

Industry/Entity Type

It Company

Number of Pages Required

2 page

Font styles to use
Other font styles liked:
• We will supply

Colors
ec1f27

Requirements
Must have
• responsive, extra small, small, medium, large, wide
Nice to have
• Modern, sophisticated, current and ON trende
Should not have
• Over saturation, keep it simple, smart and easy navigation

```html
<!DOCTYPE html>
<html lang="en">
<head>
<meta charset="utf-8">
<title>Tradelume</title>
<link href="https://fonts.googleapis.com/css2?family=Raleway:wght@500;600;700;800&family=Open+Sans:wght@400;600;700&display=swap" rel="stylesheet">
<style>
:root{
  --red:#ec1f27;
  --ink:#3a3a3a;
  --body:#6f6f6f;
  --band:#f1f1f1;
  --white:#ffffff;
  --line:#dddddd;
}
*{margin:0;padding:0;box-sizing:border-box}
html,body{width:1200px;height:2736px;overflow:hidden;background:var(--white)}
body{position:relative;font-family:"Open Sans",Arial,sans-serif;color:var(--body)}
.abs{position:absolute}
.brand{display:flex;align-items:center;gap:10px;font-family:"Raleway",Arial,sans-serif;font-weight:800;font-size:26px;letter-spacing:1px}
.brand .mark{width:26px;height:26px;border-radius:50%}
.hero{left:0;top:0;width:1200px;height:640px;background:linear-gradient(160deg,#8a96a4 0%,#5d6b7c 45%,#3d4a58 100%)}
.hero-shade{left:0;top:0;width:1200px;height:640px;background:rgba(20,28,38,.28)}
.nav{left:0;top:0;width:1200px;height:100px}
.nav .brand{position:absolute;left:70px;top:32px;color:var(--white)}
.nav .brand .mark{background:var(--white)}
.menu{position:absolute;left:432px;top:44px;display:flex;gap:34px;list-style:none}
.menu li{font-family:"Raleway",Arial,sans-serif;font-weight:700;font-size:13px;color:var(--white);letter-spacing:.5px}
.login{position:absolute;left:1020px;top:32px;width:100px;height:36px;border-radius:18px;background:var(--red);color:var(--white);font:700 13px "Raleway",Arial,sans-serif;display:flex;align-items:center;justify-content:center}
.hero-title{left:0;top:258px;width:1200px;text-align:center;font-family:"Raleway",Arial,sans-serif;font-weight:800;font-size:48px;line-height:56px;color:var(--white);letter-spacing:1px;text-transform:uppercase}
.btn-solid{height:38px;border-radius:19px;background:var(--red);color:var(--white);font:700 13px "Raleway",Arial,sans-serif;display:flex;align-items:center;justify-content:center;letter-spacing:.5px}
.dots{left:578px;top:590px;display:flex;gap:8px}
.dots span{width:10px;height:10px;border-radius:50%;background:rgba(255,255,255,.55)}
.dots span.on{background:var(--white)}
.band{left:0;width:1200px;background:var(--band)}
.section-title{font-family:"Raleway",Arial,sans-serif;font-weight:600;font-size:36px;color:var(--ink);text-transform:uppercase;letter-spacing:.5px}
.copy{font-size:15px;line-height:24px;color:var(--body);width:470px}
.btn-line{width:130px;height:38px;border:2px solid var(--red);border-radius:19px;color:var(--red);font:700 12px "Raleway",Arial,sans-serif;display:flex;align-items:center;justify-content:center;letter-spacing:.5px;background:transparent}
.photo{border-radius:2px}
.cta{left:0;top:2200px;width:1200px;height:290px;background:linear-gradient(180deg,#7b8794 0%,#4f5b68 55%,#2e3a47 100%)}
.cta-title{left:0;top:2248px;width:1200px;text-align:center;font-family:"Raleway",Arial,sans-serif;font-weight:600;font-size:40px;line-height:52px;color:var(--white);text-transform:uppercase;letter-spacing:1px}
.footer .brand{color:var(--red);font-size:24px}
.footer .brand .mark{background:var(--red);width:22px;height:22px}
.legal{font-size:11px;line-height:17px;color:#777}
.fcol h4{font:700 12px "Raleway",Arial,sans-serif;color:var(--red);letter-spacing:.5px;margin-bottom:8px;text-transform:uppercase}
.fcol li{list-style:none;font-size:11px;line-height:19px;color:#777}
.social{display:flex;gap:12px}
.social span{width:16px;height:16px;border-radius:3px;background:#9a9a9a}
.field{width:228px;height:34px;border:1px solid var(--line);border-radius:17px;font-size:11px;color:#999;display:flex;align-items:center;padding-left:14px}
.btn-small{width:92px;height:30px;border:2px solid var(--red);border-radius:15px;color:var(--red);font:700 11px "Raleway",Arial,sans-serif;display:flex;align-items:center;justify-content:center}
</style>
</head>
<body>

<header>
  <div class="abs hero" role="img" aria-label="Hands holding a tablet surrounded by floating shopping and technology icons"></div>
  <div class="abs hero-shade"></div>
  <nav class="abs nav">
    <div class="brand"><span class="mark"></span>TRADELUME</div>
    <ul class="menu">
      <li>HOME</li><li>ABOUT</li><li>SERVICES</li><li>CLIENTS</li><li>BLOG</li><li>CONTACT US</li>
    </ul>
    <div class="login">LOG IN</div>
  </nav>
  <h1 class="abs hero-title">Vestibulum vel metus sit amet<br>bibendum tincidunt</h1>
  <div class="abs btn-solid" style="left:536px;top:398px;width:128px">READ MORE</div>
  <div class="abs dots"><span></span><span class="on"></span><span></span></div>
</header>

<section>
  <h2 class="abs section-title" style="left:72px;top:708px">About Tradelume</h2>
  <p class="abs copy" style="left:72px;top:772px">Vestibulum vel metus sit amet turpis bibendum tincidunt vel sit amet quam. Pellentesque habitant morbi tristique senectus et netus et malesuada fames ac turpis egestas. Nunc consequat congue nulla eu imperdiet. Donec in est erat, ut malesuada turpis. Nunc a dui id turpis convallis semper.</p>
  <div class="abs btn-line" style="left:72px;top:946px">READ MORE</div>
  <div class="abs photo" role="img" aria-label="Shopper browsing clothing racks in a retail store" style="left:622px;top:688px;width:510px;height:218px;background:linear-gradient(120deg,#d9dde2,#b9c2cc 50%,#e4e1dc)"></div>
</section>

<section class="abs band" style="top:1070px;height:380px">
  <div class="abs photo" role="img" aria-label="Team working together at computers in a bright office" style="left:72px;top:46px;width:430px;height:290px;background:linear-gradient(120deg,#e3e4e6,#c3c7cc 55%,#8f959c)"></div>
  <h2 class="abs section-title" style="left:552px;top:64px">Retail Sectors</h2>
  <p class="abs copy" style="left:552px;top:126px">Vestibulum vel metus sit amet turpis bibendum tincidunt vel sit amet quam. Pellentesque habitant morbi tristique senectus et netus et malesuada fames ac turpis egestas consequat congue nulla eu imperdiet.</p>
  <div class="abs btn-line" style="left:552px;top:262px">READ MORE</div>
</section>

<section>
  <h2 class="abs section-title" style="left:132px;top:1494px">Shopping Industries</h2>
  <p class="abs copy" style="left:132px;top:1556px">Vestibulum vel metus sit amet turpis bibendum tincidunt vel sit amet quam. Pellentesque habitant morbi tristique senectus et netus et malesuada fames ac turpis egestas consequat congue nulla eu imperdiet.</p>
  <div class="abs btn-line" style="left:132px;top:1708px">READ MORE</div>
  <div class="abs photo" role="img" aria-label="Laptop on a desk beside colourful shopping bags" style="left:704px;top:1484px;width:428px;height:288px;background:linear-gradient(120deg,#f2eef0,#e0c6d0 50%,#c9d6e4)"></div>
</section>

<section class="abs band" style="top:1820px;height:372px">
  <div class="abs photo" role="img" aria-label="Tablet showing connected device icons held on a wooden table" style="left:72px;top:36px;width:430px;height:296px;background:linear-gradient(120deg,#c9cdd2,#a9a294 55%,#7e7566)"></div>
  <h2 class="abs section-title" style="left:552px;top:52px">IoT Firms</h2>
  <p class="abs copy" style="left:552px;top:114px">Vestibulum vel metus sit amet turpis bibendum tincidunt vel sit amet quam. Pellentesque habitant morbi tristique senectus et netus et malesuada fames ac turpis egestas consequat congue nulla eu imperdiet.</p>
  <div class="abs btn-line" style="left:552px;top:256px">READ MORE</div>
</section>

<section>
  <div class="abs cta" role="img" aria-label="Harbour city skyline with opera house at dusk"></div>
  <h2 class="abs cta-title">Australian based application building<br>technology company</h2>
  <div class="abs btn-solid" style="left:536px;top:2380px;width:128px">READ MORE</div>
</section>

<footer class="footer">
  <div class="abs brand" style="left:72px;top:2536px"><span class="mark"></span>TRADELUME</div>
  <p class="abs legal" style="left:72px;top:2580px">Copyright © 2017 Company Name.<br>All Rights Reserved.</p>
  <div class="abs social" style="left:72px;top:2630px"><span></span><span></span><span></span><span></span><span></span></div>
  <div class="abs fcol" style="left:342px;top:2536px"><h4>Product</h4><ul><li>Vestibulum</li><li>Ante ipsum primis</li><li>Faucibus orci</li><li>Luctus et ultrices</li><li>Posuere</li></ul></div>
  <div class="abs fcol" style="left:528px;top:2536px"><h4>Resources</h4><ul><li>Vestibulum</li><li>Ante ipsum primis</li><li>Faucibus orci</li><li>Luctus et ultrices</li><li>Posuere</li></ul></div>
  <div class="abs fcol" style="left:714px;top:2536px"><h4>Support</h4><ul><li>Vestibulum</li><li>Ante ipsum primis</li><li>Faucibus orci</li><li>Luctus et ultrices</li><li>Posuere</li></ul></div>
  <div class="abs fcol" style="left:888px;top:2536px"><h4>Newsletter Sign Up</h4></div>
  <div class="abs field" style="left:888px;top:2566px">Enter Email Address</div>
  <div class="abs btn-small" style="left:1024px;top:2620px">SIGN UP</div>
</footer>

</body>
</html>
```